Brightfen Business Card Redesign & Logo Update

We need to update our business cards to something more modern and fresh. Brightfen can provide the current color schemes and old design examples, but welcome creativity in helping us with this redesign. PLEASE NOTE that we no longer utilize the "tree" and/or "leaf" imagery in our branding. If able would apprecaite an update on the quality of our "words only" logo in Ai. / PNG formats too.

Target Market(s)

Investors, landowners, corporate partners, contractors

Industry/Entity Type

Environmental Restoration & Conservation

Contact Information for Business Card

Logo, persons name, title, mailing address, phone and email, website url

Font styles to use
Other font styles liked:
• Merriweather

Requirements
Nice to have
• Logo, persons name, title, mailing address, phone and email, website url, but open to ideams
Should not have
• No all back backgrounds

```html
<!DOCTYPE html>
<html lang="en">
<head>
<meta charset="utf-8">
<title>Brightfen Business Card</title>
<link rel="stylesheet" href="https://fonts.googleapis.com/css2?family=Source+Sans+3:wght@400;600;700&display=swap">
<style>
  :root {
    --bg: #e2e2e2;
    --forest: #075e30;
    --brand-green: #13793a;
    --orange: #e67a22;
    --light-orange: #f2a54a;
    --paper: #f4f4f4;
    --ink: #1a1a1a;
    --white: #ffffff;
  }
  * { margin: 0; padding: 0; box-sizing: border-box; }
  html, body {
    width: 1200px; height: 960px; overflow: hidden;
    background: var(--bg);
    font-family: "Source Sans 3", sans-serif;
  }
  .canvas { position: relative; width: 1200px; height: 960px; }

  .card {
    position: absolute; left: 297px; width: 607px; height: 347px;
    border-radius: 22px; overflow: hidden;
  }
  .card-front { top: 108px; background: var(--orange); }
  .card-front .band-top {
    position: absolute; left: 0; top: 0; width: 100%; height: 201px;
    background: var(--forest);
  }
  .card-back { top: 508px; background: var(--paper); }

  .wordmark {
    position: absolute; left: 0; width: 100%; text-align: center;
    font-weight: 700; text-transform: uppercase; line-height: 1;
    letter-spacing: 1px;
  }
  .card-front .wordmark { top: 116px; font-size: 78px; color: var(--light-orange); }
  .card-back .wordmark { top: 55px; font-size: 62px; color: var(--brand-green); }

  .tagline {
    position: absolute; left: 0; width: 100%; text-align: center;
    font-weight: 700; text-transform: uppercase; line-height: 1;
  }
  .card-front .tagline { top: 204px; font-size: 23px; color: var(--white); }
  .card-back .tagline { top: 124px; font-size: 19px; color: var(--ink); }

  .person {
    position: absolute; right: calc(607px - 285px); top: 205px; text-align: right;
  }
  .person-name { font-size: 20px; font-weight: 700; color: var(--brand-green); line-height: 26px; }
  .person-title { font-size: 15px; color: var(--ink); line-height: 22px; }

  .divider {
    position: absolute; left: 302px; top: 198px; width: 2px; height: 63px;
    background: var(--orange);
  }

  .contacts { position: absolute; left: 323px; top: 199px; list-style: none; }
  .contacts li {
    display: flex; align-items: center; gap: 5px;
    font-size: 15px; line-height: 20px; color: var(--ink);
  }
  .contacts svg { width: 14px; height: 14px; flex: none; }

  .address {
    position: absolute; left: 0; top: 294px; width: 100%; text-align: center;
    font-size: 15px; color: var(--ink);
  }
</style>
</head>
<body>
<div class="canvas">
  <section class="card card-front">
    <div class="band-top"></div>
    <div class="wordmark">Brightfen</div>
    <div class="tagline">Environmental Credit Company</div>
  </section>

  <section class="card card-back">
    <div class="wordmark">Brightfen</div>
    <div class="tagline">Environmental Credit Company</div>

    <div class="person">
      <div class="person-name">Daniel Carter</div>
      <div class="person-title">Owner</div>
    </div>

    <div class="divider"></div>

    <ul class="contacts">
      <li>
        <svg viewBox="0 0 24 24" fill="none" stroke="#e67a22" stroke-width="2.4" stroke-linecap="round" stroke-linejoin="round"><path d="M22 16.9v3a2 2 0 0 1-2.2 2 19.8 19.8 0 0 1-8.6-3.1 19.5 19.5 0 0 1-6-6A19.8 19.8 0 0 1 2.1 4.2 2 2 0 0 1 4.1 2h3a2 2 0 0 1 2 1.7c.1.9.4 1.8.7 2.7a2 2 0 0 1-.5 2.1L8 9.8a16 16 0 0 0 6 6l1.3-1.3a2 2 0 0 1 2.1-.4c.9.3 1.8.6 2.7.7a2 2 0 0 1 1.7 2z"/></svg>
        916-555-0148
      </li>
      <li>
        <svg viewBox="0 0 24 24" fill="none" stroke="#e67a22" stroke-width="2.4" stroke-linejoin="round"><rect x="2" y="4" width="20" height="16" rx="2"/><path d="M2 6l10 7 10-7"/></svg>
        daniel@brightfen.com
      </li>
      <li>
        <svg viewBox="0 0 24 24" fill="none" stroke="#e67a22" stroke-width="2.2"><circle cx="12" cy="12" r="10"/><path d="M2 12h20M12 2a15 15 0 0 1 0 20M12 2a15 15 0 0 0 0 20"/></svg>
        www.brightfen.com
      </li>
    </ul>

    <div class="address">418 Meadow Lane, Suite 210, Fairbrook, CA 95012</div>
  </section>
</div>
</body>
</html>
```